TLK Electricial Contracting Services

Hi guys, after a design for my small electrical company, have logo design files to be incorporated into the layout, the basic concept is electrical contracting services for residential, commercial, industrial & data services, image is clean clear and strong,

Card format is to have a nice clean logo on front,with maybe the Residential – commercial – industrial - data, followed with licensed & insured, followed by contact details on backside of the card.

Target Market(s)

Residential, commercial, industrial sectors.

Industry/Entity Type

Electrical

Contact Information for Business Card

TLK logo,
Residential – commercial – industrial - data
REC: 61307
Email: tlk@vornamail.net.au
Phone: 0487 352 019

Requirements
Must have
• Clean & strong design.
Nice to have
• If possible, I would like the logo colours inverted so the text is orange and the background is black on the front of the card, then the backside of the card be the reverse colour
Should not have
• No Sparks, lightning bolts,

```html
<!DOCTYPE html>
<html lang="en">
<head>
<meta charset="utf-8">
<title>TLK Electricial Contracting Services – Business Card</title>
<link rel="stylesheet" href="https://fonts.googleapis.com/css2?family=Exo+2:ital,wght@0,400;0,500;0,700;0,800;1,400&display=swap">
<style>
  :root {
    --orange: #f47b20;
    --black: #050505;
    --board: #e4e4e2;
    --board-edge: #d2d2cf;
    --page: #ffffff;
  }
  * { margin: 0; padding: 0; box-sizing: border-box; }
  html, body { width: 1200px; height: 521px; overflow: hidden; background: var(--page); }
  .canvas { position: relative; width: 1200px; height: 521px; }
  .board {
    position: absolute; left: 11px; top: 13px; width: 1178px; height: 494px;
    border-radius: 6px;
    background: radial-gradient(ellipse at 50% 50%, #f7f7f6 0%, var(--board) 75%, var(--board-edge) 100%);
  }
  .card {
    position: absolute; top: 112px; width: 522px; height: 296px; overflow: hidden;
    font-family: "Exo 2", sans-serif;
    box-shadow: 0 3px 8px rgba(0,0,0,0.25);
  }
  .card--front { left: 61px; background: var(--black); color: var(--orange); }
  .card--back { left: 621px; background: var(--orange); color: var(--black); }

  .brand-mark { font-weight: 800; letter-spacing: 2px; line-height: 1; }
  .brand-name { font-weight: 700; line-height: 1; }

  .card--front .brand-mark { position: absolute; top: 52px; left: 0; width: 100%; text-align: center; font-size: 92px; }
  .card--front .brand-name { position: absolute; top: 157px; left: 0; width: 100%; text-align: center; font-size: 20px; }
  .tagline {
    position: absolute; top: 202px; left: 0; width: 100%; text-align: center;
    font-style: italic; font-size: 16.5px; line-height: 22px;
  }

  .diagonal { position: absolute; inset: 0; width: 100%; height: 100%; }
  .card--back .brand-mark { position: absolute; top: 20px; left: 18px; font-size: 74px; }
  .card--back .brand-name { position: absolute; top: 96px; left: 26px; font-size: 15px; }
  .services { position: absolute; top: 24px; left: 274px; list-style: none; font-size: 16px; line-height: 17px; font-weight: 500; }
  .contact { position: absolute; top: 176px; left: 38px; font-weight: 500; }
  .contact p { font-size: 20px; line-height: 25px; }
  .contact .phone { font-size: 22px; }
  .corner-mark { position: absolute; top: 234px; left: 426px; color: var(--orange); text-align: center; }
  .corner-mark .brand-mark { font-size: 28px; letter-spacing: 1px; }
  .corner-mark .brand-name { font-size: 6.5px; }
</style>
</head>
<body>
<div class="canvas">
  <div class="board"></div>

  <section class="card card--front">
    <div class="brand-mark">TLK</div>
    <div class="brand-name">Tara Lee Kent Electrical</div>
    <p class="tagline">Electrical contracting services for residential,<br>commercial, industrial &amp; data services.</p>
  </section>

  <section class="card card--back">
    <svg class="diagonal" viewBox="0 0 522 296" preserveAspectRatio="none" aria-hidden="true">
      <polygon points="516,0 522,0 522,296 296,296" fill="var(--black)"/>
    </svg>
    <div class="brand-mark">TLK</div>
    <div class="brand-name">Tara Lee Kent Electrical</div>
    <ul class="services">
      <li>Residential</li>
      <li>Commercial</li>
      <li>Industrial</li>
      <li>Data</li>
      <li>REC: 61307</li>
    </ul>
    <div class="contact">
      <p>E-mail: tlk@vornamail.net.au</p>
      <p class="phone">Phone: 0487 352 019</p>
    </div>
    <div class="corner-mark">
      <div class="brand-mark">TLK</div>
      <div class="brand-name">Tara Lee Kent Electrical</div>
    </div>
  </section>
</div>
</body>
</html>
```